Website update for Harborline Ledger Partners & Bookkeeping

Our website needs updating
www.harborlineledgerpartners.com
Here are some of our latest print pieces to use as a guide?
I have also attached our graphic identity guide which includes the Pantone colors

Target Market(s)

Insurance Agencies

Industry/Entity Type

Accounting

Number of Pages Required

5+ page

```html
<!DOCTYPE html>
<html lang="en">
<head>
<meta charset="utf-8">
<title>Harborline Ledger Partners &amp; Bookkeeping</title>
<link href="https://fonts.googleapis.com/css2?family=Montserrat:wght@400;600;700&family=Open+Sans:wght@400;600;700&display=swap" rel="stylesheet">
<style>
:root{
  --teal:#16a39a;
  --teal-dark:#0f7f78;
  --ink:#2a2a2a;
  --muted:#7a7a7a;
  --line:#e4e4e4;
  --dark:#262626;
  --darker:#1c1c1c;
  --white:#ffffff;
  --soft:#f6f7f7;
  --icon-dim:#555555;
}
*{box-sizing:border-box;margin:0;padding:0}
html,body{width:1200px;height:2724px;overflow:hidden}
body{font-family:"Open Sans",Arial,sans-serif;color:var(--ink);background:var(--white);position:relative}

/* header */
.site-header{position:absolute;top:0;left:0;width:1200px;height:62px;background:var(--white);z-index:3;display:flex;align-items:center;justify-content:space-between;padding:0 70px 0 60px;box-shadow:0 1px 4px rgba(0,0,0,.08)}
.brand{display:flex;align-items:center;gap:10px}
.brand-mark{width:30px;height:30px;background:var(--teal)}
.brand-name{font-family:"Montserrat",Arial,sans-serif;font-weight:700;font-size:13px;line-height:1.25;color:var(--teal);width:190px}
.nav{display:flex;gap:34px;list-style:none}
.nav li{font-family:"Montserrat",Arial,sans-serif;font-size:11px;font-weight:600;letter-spacing:.5px;color:var(--ink);white-space:nowrap}

/* hero */
.hero{position:absolute;top:0;left:0;width:1200px;height:600px;background:linear-gradient(100deg,#eef1f2 0%,#dfe5e8 40%,#c9d1d6 70%,#aeb8bf 100%)}
.hero-copy{position:absolute;left:60px;top:190px;width:480px}
.hero-brand{font-family:"Montserrat",Arial,sans-serif;font-weight:700;font-size:40px;line-height:1.05;color:var(--white)}
.hero-tag{margin-top:18px;font-family:"Montserrat",Arial,sans-serif;font-weight:700;font-size:17px;line-height:1.35;color:var(--teal-dark);text-transform:uppercase}
.btn{display:inline-block;background:var(--teal);color:var(--white);font-family:"Montserrat",Arial,sans-serif;font-weight:600;font-size:11px;letter-spacing:.8px;padding:12px 22px;text-transform:uppercase;white-space:nowrap}
.hero .btn{margin-top:26px}

/* welcome */
.welcome{position:absolute;top:600px;left:0;width:1200px;height:560px;text-align:center;background:var(--white)}
.welcome h1{margin-top:62px;font-family:"Montserrat",Arial,sans-serif;font-weight:600;font-size:30px;color:var(--ink);letter-spacing:.5px}
.welcome h2{margin-top:6px;font-family:"Montserrat",Arial,sans-serif;font-weight:400;font-size:22px;color:var(--teal);text-transform:uppercase}
.intro{width:840px;margin:22px auto 0;font-size:12px;line-height:1.75;color:var(--muted)}
.services{display:flex;justify-content:center;gap:110px;margin-top:40px}
.service{width:200px}
.service-icon{width:74px;height:74px;margin:0 auto;border-radius:50%;background:var(--teal);display:flex;align-items:center;justify-content:center}
.service h3{margin-top:18px;font-family:"Montserrat",Arial,sans-serif;font-weight:700;font-size:12px;line-height:1.4;color:var(--ink);text-transform:uppercase}
.service p{margin-top:30px;font-size:11px;line-height:1.7;color:var(--muted)}
.dots{display:flex;justify-content:center;gap:8px;margin-top:30px}
.dots span{width:7px;height:7px;border-radius:50%;background:#cfcfcf}
.dots span.on{background:var(--teal)}

/* about */
.about{position:absolute;top:1160px;left:0;width:1200px;height:330px;background:linear-gradient(90deg,#1f2426 0%,#2f3638 50%,#1c2022 100%);text-align:center;color:var(--white)}
.about h2{margin-top:70px;font-family:"Montserrat",Arial,sans-serif;font-weight:600;font-size:28px;letter-spacing:.5px}
.about p{width:840px;margin:18px auto 0;font-size:12px;line-height:1.75;color:#d4d4d4}
.about .btn{margin-top:26px}

/* why */
.why{position:absolute;top:1490px;left:0;width:1200px;height:510px;text-align:center}
.section-title{font-family:"Montserrat",Arial,sans-serif;font-weight:700;font-size:30px;color:var(--ink)}
.why .section-title{margin-top:56px}
.rule{width:90px;height:2px;background:var(--teal);margin:14px auto 0}
.reasons{display:flex;justify-content:center;gap:24px;margin-top:40px;text-align:left}
.reason{width:232px}
.reason-photo{width:232px;height:152px}
.reason h3{margin-top:18px;font-family:"Montserrat",Arial,sans-serif;font-weight:700;font-size:11px;color:var(--ink);text-transform:uppercase}
.reason p{margin-top:10px;font-size:11px;line-height:1.7;color:var(--muted)}

/* testimonial */
.testimonial{position:absolute;top:2000px;left:0;width:1200px;height:360px;text-align:center}
.testimonial .section-title{margin-top:20px}
.quote-row{display:flex;align-items:center;width:900px;margin:48px auto 0;gap:60px;text-align:left}
.avatar{width:170px;height:170px;border-radius:50%;background:radial-gradient(circle at 50% 40%,#d9d9d9,#9a9a9a);flex:none}
.quote{position:relative;padding:0 40px}
.quote p{font-size:12px;line-height:1.8;color:var(--muted);font-style:italic}
.quote .who{margin-top:16px;font-family:"Montserrat",Arial,sans-serif;font-weight:700;font-size:13px;color:var(--teal);font-style:normal}
.quote .role{font-size:11px;color:var(--muted);font-style:normal;margin-top:2px}
.qmark{position:absolute;font-family:"Montserrat",Arial,sans-serif;font-size:54px;color:#cccccc;line-height:1}

/* footer */
.site-footer{position:absolute;top:2360px;left:0;width:1200px;height:320px;background:var(--dark);color:#bdbdbd;display:flex;padding:56px 60px 0;gap:60px}
.foot-brand{width:260px;display:flex;gap:12px;align-items:flex-start}
.foot-brand .brand-mark{width:40px;height:40px;flex:none}
.foot-brand .brand-name{font-size:19px;width:200px;line-height:1.25}
.foot-col h4{font-family:"Montserrat",Arial,sans-serif;font-weight:700;font-size:13px;color:var(--white);text-transform:uppercase;margin-bottom:18px}
.foot-how{width:300px}
.foot-how p{font-size:11px;line-height:1.8}
.foot-how .more{margin-top:14px;font-size:11px;color:var(--white);font-weight:600}
.foot-links{width:180px;list-style:none}
.foot-links li{font-size:11px;line-height:2}
.foot-contact{width:230px}
.contact-line{display:flex;gap:10px;font-size:11px;line-height:1.7;margin-bottom:10px}
.contact-line svg{flex:none;margin-top:3px}
.bottom-bar{position:absolute;top:2680px;left:0;width:1200px;height:44px;background:var(--darker);display:flex;align-items:center;justify-content:space-between;padding:0 60px;font-size:10px;color:#8f8f8f}
.bottom-right{display:flex;align-items:center;gap:28px}
.legal{white-space:nowrap}
.social{display:flex;gap:10px;align-items:center}
.social-dot{display:block;width:14px;height:14px;border-radius:50%;background:var(--icon-dim)}
</style>
</head>
<body>

<header class="site-header">
  <div class="brand"><span class="brand-mark"></span><span class="brand-name">Harborline Ledger Partners &amp; Bookkeeping</span></div>
  <ul class="nav">
    <li>ABOUT US</li><li>OVERVIEW</li><li>OUR SERVICES</li><li>HOW IT WORKS</li><li>RESOURCES</li><li>BLOG</li>
  </ul>
</header>

<section class="hero" role="img" aria-label="Photo of two businesswomen talking in a bright office with a tablet">
  <div class="hero-copy">
    <div class="hero-brand">HLP</div>
    <p class="hero-tag">Specialists in providing accounting support services to independent insurance agencies</p>
    <span class="btn">Contact Now</span>
  </div>
</section>

<section class="welcome">
  <h1>WELCOME TO HLP</h1>
  <h2>Harborline Ledger Partners &amp; Bookkeeping</h2>
  <p class="intro">Dana Whitford is an accounting professional with more than 16 years of experience in accounting, budgeting and financial reporting for independent insurance agencies. She has a proven track record of improving efficiency in agency bookkeeping and implementing technology initiatives throughout her career.</p>
  <div class="services">
    <div class="service">
      <div class="service-icon"><svg width="36" height="36" viewBox="0 0 36 36" fill="none" stroke="#fff" stroke-width="2"><circle cx="18" cy="18" r="14"/><path d="M4 18h28M18 4c5 4 5 24 0 28M18 4c-5 4-5 24 0 28"/></svg></div>
      <h3>Direct Bill<br>Commission Tracking</h3>
      <p>We follow every carrier direct bill payment so no commission slips past your agency.</p>
    </div>
    <div class="service">
      <div class="service-icon"><svg width="32" height="36" viewBox="0 0 32 36" fill="none" stroke="#fff" stroke-width="2"><path d="M4 2h18l6 6v26H4z"/><path d="M16 12v14M20 15h-6a2.5 2.5 0 0 0 0 5h4a2.5 2.5 0 0 1 0 5h-6"/></svg></div>
      <h3>Agency Bill<br>Statements Reconciled</h3>
      <p>Monthly agency bill statements are matched line by line against your own records.</p>
    </div>
    <div class="service">
      <div class="service-icon"><svg width="38" height="34" viewBox="0 0 38 34" fill="none" stroke="#fff" stroke-width="2"><circle cx="19" cy="10" r="7"/><path d="M5 32c2-8 8-12 14-12s12 4 14 12"/></svg></div>
      <h3>Customer<br>Payments Posted</h3>
      <p>Client payments are posted promptly and accurately so your receivables stay current.</p>
    </div>
  </div>
  <div class="dots"><span class="on"></span><span></span><span></span></div>
</section>

<section class="about" role="img" aria-label="Dark photo of an accountant working at a desk with a calculator">
  <h2>ABOUT HLP</h2>
  <p>Dana Whitford is an accounting professional with more than 16 years of experience in accounting, budgeting and financial reporting for independent insurance agencies. She has a proven track record of improving efficiency in agency bookkeeping and implementing technology initiatives throughout her career.</p>
  <span class="btn">Read More Info</span>
</section>

<section class="why">
  <h2 class="section-title">WHY IT WORKS?</h2>
  <div class="rule"></div>
  <div class="reasons">
    <div class="reason">
      <div class="reason-photo" role="img" aria-label="Photo of a team meeting around a table" style="background:linear-gradient(135deg,#c9d6dd,#8ea4b0)"></div>
      <h3>Educated &amp; Trained Staff</h3>
      <p>Our staff are trained in agency accounting and bring years of focused insurance experience.</p>
    </div>
    <div class="reason">
      <div class="reason-photo" role="img" aria-label="Photo of hands reviewing printed reports" style="background:linear-gradient(135deg,#e2e2e2,#a9a9a9)"></div>
      <h3>Quality Control</h3>
      <p>Every reconciliation is reviewed twice before it reaches you, keeping your books reliable.</p>
    </div>
    <div class="reason">
      <div class="reason-photo" role="img" aria-label="Photo of colleagues working together at laptops" style="background:linear-gradient(135deg,#d7dde0,#96a2a8)"></div>
      <h3>Separation of Duties</h3>
      <p>Different people handle entry and review, protecting your agency from errors and fraud.</p>
    </div>
    <div class="reason">
      <div class="reason-photo" role="img" aria-label="Blue digital image of a padlock on a circuit board" style="background:linear-gradient(135deg,#1f4f86,#0c2547)"></div>
      <h3>Data Security</h3>
      <p>Your financial data is stored on encrypted systems with strict access controls at all times.</p>
    </div>
  </div>
</section>

<section class="testimonial">
  <h2 class="section-title">WHAT OUR CLIENT'S SAY</h2>
  <div class="rule"></div>
  <div class="quote-row">
    <div class="avatar" role="img" aria-label="Portrait photo of a smiling client"></div>
    <div class="quote">
      <span class="qmark" style="left:0;top:-18px">&ldquo;</span>
      <p>Since handing our bookkeeping to this team, our commission statements finally balance every month. They are responsive, careful and always explain the numbers clearly, which gives us more time to focus on our clients.</p>
      <p class="who">Marcus Hale</p>
      <p class="role">Business owner</p>
      <span class="qmark" style="right:0;bottom:-40px">&rdquo;</span>
    </div>
  </div>
</section>

<footer class="site-footer">
  <div class="foot-brand"><span class="brand-mark"></span><span class="brand-name">Harborline Ledger Partners &amp; Bookkeeping</span></div>
  <div class="foot-col foot-how">
    <h4>How It Works?</h4>
    <p>We take over the daily accounting work of your agency, reconcile carrier statements, post payments and deliver clear monthly reports so you always know where you stand.</p>
    <p class="more">Read more &rarr;</p>
  </div>
  <div class="foot-col">
    <h4>Welcome</h4>
    <ul class="foot-links">
      <li>Home</li><li>About Us</li><li>Overview</li><li>Our Services</li><li>How It Works</li><li>Resources</li><li>Contact Us</li>
    </ul>
  </div>
  <div class="foot-col foot-contact">
    <h4>Contact Info</h4>
    <div class="contact-line"><svg width="10" height="14" viewBox="0 0 10 14"><path d="M5 0a5 5 0 0 1 5 5c0 4-5 9-5 9S0 9 0 5a5 5 0 0 1 5-5z" fill="#16a39a"/><circle cx="5" cy="5" r="2" fill="#262626"/></svg><span>1284 Harbor Point Road, Suite 210<br>Portland, ME 04101</span></div>
    <div class="contact-line"><svg width="12" height="12" viewBox="0 0 12 12"><path d="M2 0h3l1 3-2 1a7 7 0 0 0 4 4l1-2 3 1v3a1 1 0 0 1-1 1C5 11 1 7 1 1a1 1 0 0 1 1-1z" fill="#16a39a"/></svg><span>(207) 555-0148</span></div>
    <div class="contact-line"><svg width="12" height="10" viewBox="0 0 12 10"><rect width="12" height="10" fill="#16a39a"/><path d="M0 0l6 5 6-5" fill="none" stroke="#262626" stroke-width="1.2"/></svg><span>hello@harborlineledgerpartners.com</span></div>
    <div class="contact-line"><svg width="12" height="12" viewBox="0 0 12 12"><circle cx="6" cy="6" r="5.5" fill="none" stroke="#16a39a"/><path d="M.5 6h11M6 .5c3 3 3 8 0 11M6 .5c-3 3-3 8 0 11" fill="none" stroke="#16a39a" stroke-width=".8"/></svg><span>www.harborlineledgerpartners.com</span></div>
  </div>
</footer>

<div class="bottom-bar">
  <span>&copy; 2024 HLP. All rights reserved.</span>
  <div class="bottom-right">
    <span class="legal">Terms of use | Privacy policy</span>
    <div class="social"><span class="social-dot"></span><span class="social-dot"></span><span class="social-dot"></span><span class="social-dot"></span><span class="social-dot"></span></div>
  </div>
</div>

</body>
</html>
```